Investment company needing business card

We are wanting a business card which looks sharp and easy on the eye. We are thinking of having a business card with the logo embossed on it, to really make it stand out. We will only have a small amount of information of the business card, person's name, position, email address and phone number

Contact Information for Business Card

Danielle Frost
Executive Assistant
+64 21 473 5162
danielf@harwickpartners.co.nz

Requirements
Must have
• Embossed logo
Should not have
• Not to be busy

```html
<!DOCTYPE html>
<html lang="en">
<head>
<meta charset="utf-8">
<title>Harwick Partners – Business Card</title>
<link rel="stylesheet" href="https://fonts.googleapis.com/css2?family=Lato:wght@400;700&family=Michroma&display=swap">
<style>
  :root {
    --page-bg: #2a2b2e;
    --card-back: #5d5e61;
    --card-back-emboss: #2b2b2d;
    --card-front: #ffffff;
    --brand-green: #1fa862;
    --ink-grey: #58595b;
    --rule-grey: #8a8b8d;
  }
  * { box-sizing: border-box; margin: 0; padding: 0; }
  html, body { width: 1200px; height: 800px; overflow: hidden; }
  body {
    background: var(--page-bg);
    position: relative;
    font-family: "Lato", sans-serif;
  }
  .card {
    position: absolute;
    width: 560px;
    height: 320px;
    box-shadow: 0 18px 40px rgba(0,0,0,.45);
  }
  .card--back {
    left: 80px; top: 90px;
    background: var(--card-back);
    display: flex; align-items: center; justify-content: center;
  }
  .card--front {
    left: 560px; top: 390px;
    background: var(--card-front);
  }
  .wordmark {
    display: flex; align-items: center; gap: 14px;
    font-family: "Michroma", sans-serif;
    font-weight: 400;
    letter-spacing: 2px;
    text-transform: uppercase;
  }
  .wordmark__square { width: 34px; height: 34px; }
  .card--back .wordmark { font-size: 30px; color: var(--card-back-emboss); }
  .card--back .wordmark__square { background: var(--card-back-emboss); width: 46px; height: 46px; }
  .card--back .wordmark__name { text-shadow: 0 1px 0 rgba(255,255,255,.18); }
  .card--front .wordmark {
    position: absolute; left: 36px; top: 42px;
    font-size: 20px; color: var(--brand-green);
  }
  .card--front .wordmark__square { background: var(--brand-green); }
  .card__rule {
    position: absolute; left: 0; top: 0;
  }
  .contact {
    position: absolute; left: 36px; bottom: 32px;
    color: var(--ink-grey);
  }
  .contact__headline { display: flex; align-items: baseline; gap: 8px; margin-bottom: 8px; }
  .contact__name {
    color: var(--brand-green); font-weight: 700; font-size: 17px;
    text-transform: uppercase; letter-spacing: .3px;
  }
  .contact__divider { font-size: 16px; color: var(--ink-grey); }
  .contact__role { font-size: 14px; }
  .contact__line {
    width: 300px; height: 1px; background: var(--rule-grey); margin-bottom: 10px;
  }
  .contact__item { display: flex; align-items: center; gap: 8px; font-size: 13px; margin-bottom: 4px; }
  .contact__icon { width: 12px; height: 12px; flex: none; }
</style>
</head>
<body>
  <section class="card card--back" aria-label="Business card back">
    <div class="wordmark">
      <span class="wordmark__square"></span>
      <span class="wordmark__name">Harwick Partners</span>
    </div>
  </section>

  <section class="card card--front" aria-label="Business card front">
    <svg class="card__rule" width="560" height="320" aria-hidden="true">
      <line x1="36" y1="98" x2="300" y2="98" stroke="var(--rule-grey)" stroke-width="1"/>
      <line x1="330" y1="210" x2="540" y2="140" stroke="var(--rule-grey)" stroke-width="1"/>
    </svg>
    <div class="wordmark">
      <span class="wordmark__square"></span>
      <span class="wordmark__name">Harwick Partners</span>
    </div>

    <div class="contact">
      <div class="contact__headline">
        <span class="contact__name">Danielle Frost</span>
        <span class="contact__divider">|</span>
        <span class="contact__role">Executive Assistant</span>
      </div>
      <div class="contact__line"></div>
      <div class="contact__item">
        <svg class="contact__icon" viewBox="0 0 12 12" aria-hidden="true">
          <rect x="2.5" y="0.8" width="7" height="10.4" rx="1.2" fill="none" stroke="var(--brand-green)" stroke-width="1.2"/>
        </svg>
        <span>+64 21 473 5162</span>
      </div>
      <div class="contact__item">
        <svg class="contact__icon" viewBox="0 0 12 12" aria-hidden="true">
          <rect x="0.5" y="2" width="11" height="8" fill="var(--brand-green)"/>
          <path d="M0.5 2 L6 6.5 L11.5 2" fill="none" stroke="#fff" stroke-width="1"/>
        </svg>
        <span>danielf@harwickpartners.co.nz</span>
      </div>
    </div>
  </section>
</body>
</html>
```